Business card for event manager / organizer "waiter service"

Draft of a new valuable business card for my company.
Events, personnel service providers, festivals

```html
<!DOCTYPE html>
<html lang="de">
<head>
<meta charset="utf-8">
<title>Jonas´ Kellnerservice – Visitenkarte</title>
<link href="https://fonts.googleapis.com/css2?family=Montserrat:wght@400;500;600;700&display=swap" rel="stylesheet">
<style>
  :root {
    --bg: #3a3a3c;
    --card-dark: #221e22;
    --orange: #ef7d1a;
    --white: #ffffff;
    --muted: #e6e3e6;
  }
  * { margin: 0; padding: 0; box-sizing: border-box; }
  html, body { width: 1200px; height: 689px; overflow: hidden; }
  body {
    background: var(--bg);
    font-family: "Montserrat", sans-serif;
    position: relative;
  }
  .card {
    position: absolute;
    top: 180px;
    width: 540px;
    height: 330px;
    border-radius: 22px;
    overflow: hidden;
    box-shadow: 0 18px 40px rgba(0,0,0,.45);
  }
  /* Front */
  .card-front { left: 30px; background: var(--card-dark); }
  .front-scene {
    position: absolute; inset: 0;
    background:
      radial-gradient(ellipse at 78% 8%, rgba(240,150,40,.85), rgba(240,150,40,0) 45%),
      radial-gradient(ellipse at 30% 20%, rgba(170,110,220,.7), rgba(170,110,220,0) 50%),
      linear-gradient(180deg, #5a3570 0%, #3a2344 50%, #1f1a22 100%);
  }
  .front-brand {
    position: absolute; left: 56px; top: 112px;
    display: flex; align-items: center; gap: 18px;
  }
  .brand-mark {
    width: 74px; height: 74px; border-radius: 50%;
    background: var(--orange);
    flex: none;
  }
  .brand-name {
    color: var(--white); font-weight: 700;
    font-size: 36px; line-height: 1.05; letter-spacing: .5px;
  }
  .brand-name-line { display: block; white-space: nowrap; }
  .brand-tagline {
    color: var(--white); font-weight: 400; font-size: 14px;
    margin-top: 8px; letter-spacing: .3px; white-space: nowrap;
  }
  /* Back */
  .card-back { left: 630px; background: var(--card-dark); }
  .back-photo {
    position: absolute; left: 14px; bottom: 14px;
    width: 220px; height: 250px; border-radius: 16px;
    background: radial-gradient(ellipse at 45% 35%, #6d6d70, #2a2a2c 75%);
  }
  .back-stripes { position: absolute; inset: 0; }
  .back-info {
    position: absolute; right: 28px; top: 26px;
    text-align: right;
  }
  .back-brand {
    display: flex; align-items: center; justify-content: flex-end; gap: 10px;
  }
  .back-brand .brand-mark { width: 34px; height: 34px; }
  .back-brand .brand-name { font-size: 19px; white-space: nowrap; }
  .back-brand .brand-tagline { font-size: 8px; margin-top: 3px; }
  .person-name {
    margin-top: 22px; color: var(--white);
    font-weight: 500; font-size: 27px; letter-spacing: .3px; white-space: nowrap;
  }
  .person-role {
    color: var(--orange); font-weight: 500; font-size: 14px; margin-top: 2px;
  }
  .contact-list { list-style: none; margin-top: 16px; }
  .contact-item {
    display: flex; align-items: center; justify-content: flex-end; gap: 8px;
    color: var(--muted); font-size: 12.5px; line-height: 20px; white-space: nowrap;
  }
  .contact-icon { width: 12px; height: 12px; flex: none; }
</style>
</head>
<body>

<section class="card card-front" aria-label="Vorderseite">
  <div class="front-scene" role="img" aria-label="Konzertpublikum mit erhobenen Händen vor violettem und orangem Bühnenlicht"></div>
  <div class="front-brand">
    <span class="brand-mark"></span>
    <div>
      <div class="brand-name">
        <span class="brand-name-line">Jonas´</span>
        <span class="brand-name-line">Kellnerservice</span>
      </div>
      <div class="brand-tagline">…weil jedes Fest gute Gastgeber verdient!</div>
    </div>
  </div>
</section>

<section class="card card-back" aria-label="Rückseite">
  <svg class="back-stripes" width="540" height="330" viewBox="0 0 540 330">
    <line x1="150" y1="120" x2="255" y2="330" stroke="var(--orange)" stroke-width="4"/>
    <line x1="175" y1="120" x2="280" y2="330" stroke="var(--orange)" stroke-width="2"/>
  </svg>
  <div class="back-photo" role="img" aria-label="Porträt des Inhabers in weißem Hemd und schwarzer Weste mit verschränkten Armen"></div>

  <div class="back-info">
    <div class="back-brand">
      <span class="brand-mark"></span>
      <div>
        <div class="brand-name">Jonas´ Kellnerservice</div>
        <div class="brand-tagline">…weil jedes Fest gute Gastgeber verdient!</div>
      </div>
    </div>
    <div class="person-name">Jonas Berenfeld</div>
    <div class="person-role">Inhaber</div>
    <ul class="contact-list">
      <li class="contact-item">02361 555 01 23
        <svg class="contact-icon" viewBox="0 0 12 12"><path d="M2 1.5l2 0 1 2.5-1.2 1a6 6 0 0 0 3.2 3.2l1-1.2 2.5 1v2a1 1 0 0 1-1 1A9 9 0 0 1 1 2.5a1 1 0 0 1 1-1z" fill="var(--orange)"/></svg></li>
      <li class="contact-item">0170 555 48 12
        <svg class="contact-icon" viewBox="0 0 12 12"><rect x="3" y="0.8" width="6" height="10.4" rx="1.2" fill="none" stroke="var(--orange)" stroke-width="1.3"/><circle cx="6" cy="9.3" r=".7" fill="var(--orange)"/></svg></li>
      <li class="contact-item">info@jonas-kellnerservice.de
        <svg class="contact-icon" viewBox="0 0 12 12"><path d="M1 6L11 1 8 11 6 7z" fill="var(--orange)"/></svg></li>
      <li class="contact-item">jonas-kellnerservice.de
        <svg class="contact-icon" viewBox="0 0 12 12"><circle cx="6" cy="6" r="5" fill="none" stroke="var(--orange)" stroke-width="1.2"/><ellipse cx="6" cy="6" rx="2.2" ry="5" fill="none" stroke="var(--orange)" stroke-width="1"/><line x1="1" y1="6" x2="11" y2="6" stroke="var(--orange)" stroke-width="1"/></svg></li>
      <li class="contact-item">Lindenweg 12, 45657 Marlheim
        <svg class="contact-icon" viewBox="0 0 12 12"><path d="M6 11.5S2 7 2 4.5a4 4 0 0 1 8 0C10 7 6 11.5 6 11.5z" fill="var(--orange)"/><circle cx="6" cy="4.5" r="1.4" fill="var(--card-dark)"/></svg></li>
      <li class="contact-item">/jonaskellnerservice
        <svg class="contact-icon" viewBox="0 0 12 12"><circle cx="6" cy="6" r="5.5" fill="var(--orange)"/></svg></li>
    </ul>
  </div>
</section>

</body>
</html>
```